Design and Renovation Company Luxury Business Card

I want to create a luxury business card for a Design and Renovation Firm . We will use our current logo. The company name is 528BUILDA. We do not want anything standard. We need a very unique concept.
Please see uploaded inspiration. I really like the textured paper option. I would like the card to be thick with debossing, and/or embossing options. The logo has orange in it but I would like to see the card with and without the orange. I think the orange may make the company feel less high-end. The goal is to elevate the logo not match its vibe per se of the logo. We want something very unique, not standard at all!
I would like a space for :
Logo,
Name,
Position,
Email,
Office number,
Website Address,
Business Address,
Thank you!
Have fun!
Target Market(s)
Home owners Age 35 +
Industry/Entity Type
Design and Renovation
Contact Information for Business Card
Logo, Name, Position, Email, Office number, Website Address, Business Address,.
Colors
Designer to choose colors to be used in the design.
Requirements
Must have
- A luxury designer feel. Must be black or dark grey but open to other luxury ideas.
Nice to have
- Gold, silver, black embossing or debossing. Textured paper design.
Should not have
- A cheap look and feel.

```html
<!DOCTYPE html>
<html lang="en">
<head>
<meta charset="utf-8">
<title>528BUILDA Business Card</title>
<link href="https://fonts.googleapis.com/css2?family=Montserrat:wght@400;600&family=Poppins:wght@300;400&display=swap" rel="stylesheet">
<style>
  :root {
    --backdrop: #2e2e2e;
    --card: #222222;
    --gold: #d9a23f;
    --gold-light: #e8b95a;
    --gold-soft: #c8963e;
    --shadow: rgba(0, 0, 0, 0.55);
  }
  * { margin: 0; padding: 0; box-sizing: border-box; }
  html, body { width: 1200px; height: 900px; overflow: hidden; }
  body { background: var(--backdrop); position: relative; font-family: "Poppins", sans-serif; }

  .card {
    position: absolute;
    left: 362px;
    width: 475px;
    height: 271px;
    background: var(--card);
    box-shadow: 0 6px 14px var(--shadow);
  }
  .card--front { top: 177px; }
  .card--back { top: 494px; }

  .holder { position: absolute; left: 32px; top: 28px; }
  .holder__name {
    font-family: "Montserrat", sans-serif;
    font-weight: 400;
    font-size: 19px;
    letter-spacing: 0.06em;
    color: var(--gold);
    line-height: 1.1;
  }
  .holder__name strong { font-weight: 600; color: var(--gold-light); }
  .holder__role {
    font-family: "Poppins", sans-serif;
    font-weight: 300;
    font-size: 15px;
    color: var(--gold-soft);
    margin-top: 4px;
  }

  .address {
    position: absolute; left: 32px; top: 146px;
    font-weight: 300; font-size: 11px; line-height: 15px;
    letter-spacing: 0.04em; color: var(--gold-soft);
  }
  .contacts {
    position: absolute; left: 32px; top: 186px;
    list-style: none;
  }
  .contacts__item {
    display: flex; align-items: center; gap: 5px;
    font-weight: 300; font-size: 11.5px; letter-spacing: 0.03em;
    color: var(--gold-soft); height: 19px;
  }
  .contacts__icon { width: 10px; height: 10px; fill: var(--gold); flex: none; }

  .front-brand { position: absolute; right: 31px; top: 82px; text-align: right; }
  .front-brand__square {
    display: block; width: 56px; height: 56px;
    background: var(--gold); margin: 0 0 14px auto;
  }
  .front-brand__name {
    font-family: "Montserrat", sans-serif;
    font-weight: 400; font-size: 22px; letter-spacing: 0.14em;
    color: var(--gold); line-height: 1;
  }

  .back-brand {
    position: absolute; left: 0; right: 0; top: 0; bottom: 0;
    display: flex; align-items: center; justify-content: center; gap: 14px;
  }
  .back-brand__square { width: 34px; height: 34px; background: var(--gold); }
  .back-brand__name {
    font-family: "Montserrat", sans-serif;
    font-weight: 400; font-size: 38px; letter-spacing: 0.12em;
    color: var(--gold); line-height: 1;
  }
</style>
</head>
<body>
  <section class="card card--front">
    <div class="holder">
      <p class="holder__name">DANIEL M. <strong>HARTWELL</strong></p>
      <p class="holder__role">Managing Director</p>
    </div>

    <p class="address">2715 Harbor View Avenue<br>Portland, OR 97204</p>

    <ul class="contacts">
      <li class="contacts__item">
        <svg class="contacts__icon" viewBox="0 0 24 24" aria-hidden="true"><path d="M6.6 10.8a15.1 15.1 0 0 0 6.6 6.6l2.2-2.2c.3-.3.7-.4 1-.2 1.1.4 2.3.6 3.6.6.6 0 1 .4 1 1V20c0 .6-.4 1-1 1A17 17 0 0 1 3 4c0-.6.4-1 1-1h3.5c.6 0 1 .4 1 1 0 1.3.2 2.5.6 3.6.1.3 0 .7-.2 1z"/></svg>
        +00 987 654 32
      </li>
      <li class="contacts__item">
        <svg class="contacts__icon" viewBox="0 0 24 24" aria-hidden="true"><path d="M2 5h20v14H2z M4 7v.5l8 5 8-5V7l-8 5z" fill-rule="evenodd"/></svg>
        hello@528builda.com
      </li>
      <li class="contacts__item">
        <svg class="contacts__icon" viewBox="0 0 24 24" aria-hidden="true"><path d="M12 2a10 10 0 1 0 0 20 10 10 0 0 0 0-20zm6.9 6h-3a15.7 15.7 0 0 0-1.3-3.6A8 8 0 0 1 18.9 8zM12 4c.8 1.2 1.5 2.5 1.9 4h-3.8c.4-1.5 1.1-2.8 1.9-4zM4.3 14a8.2 8.2 0 0 1 0-4h3.4a16 16 0 0 0 0 4zm.8 2h3a15.7 15.7 0 0 0 1.3 3.6A8 8 0 0 1 5.1 16zm3-8h-3a8 8 0 0 1 4.3-3.6C8.8 5.5 8.4 6.7 8.1 8zM12 20c-.8-1.2-1.5-2.5-1.9-4h3.8c-.4 1.5-1.1 2.8-1.9 4zm2.3-6H9.7a14.6 14.6 0 0 1 0-4h4.6a14.6 14.6 0 0 1 0 4zm.3 5.6c.6-1.1 1-2.3 1.3-3.6h3a8 8 0 0 1-4.3 3.6zm1.7-5.6a16 16 0 0 0 0-4h3.4a8.2 8.2 0 0 1 0 4z"/></svg>
        www.528builda.com
      </li>
    </ul>

    <div class="front-brand">
      <span class="front-brand__square" aria-hidden="true"></span>
      <p class="front-brand__name">528BUILDA</p>
    </div>
  </section>

  <section class="card card--back">
    <div class="back-brand">
      <span class="back-brand__square" aria-hidden="true"></span>
      <p class="back-brand__name">528BUILDA</p>
    </div>
  </section>
</body>
</html>
```